Counseling Practice Business Card

I need a professional looking business card incorporating my new logo that was just completed. Card needs to incorporate my name and title, description of my specialty, my address, my phone number, my fax number, my email and my website URL. I need to be able to choose design on/with different paper colors and textures.
I do not have a lot of business card ideas so I am open to anything but I want bold,sharp, clear card without additional designs other than my logo (see attached file info). I am open to different color backgrounds or paper colors including black. I do not like traditional brackets around area codes in phone number or dashes between numbers in phone number. Am open to other ways of presenting including periods between numbers as appropriate. I do not know enough to know what I like yet but I want card to coordinate and work together with my logo. My practice emphasizes natural mental health interventions so any use of color (with background paper color or the blue and green in my logo) that elicits nature is nice. In addition to black, any natural brown or wood looking background might be desirable also. Most of the offerings so far look very similar and boring.

Target Market(s)

Potential therapy clients and other professionals

Contact Information for Business Card

Card information:
Gerald M. Whitcombe, Ph.D.
Licensed Clinical Psychologist
Integrative Health Coach
4812 Marlowe Ridge Blvd SE
Suite 310
Duluth, GA 30096
(770) 415-2983 phone
(770) 581-4096 fax
drgeraldwhitcombe@quillmarsh.net
brightfernwellness.net

Font styles to use
Serif
Sans Serif
Other font styles liked:
• anything that you think looks crisp, clear and easily readable

Requirements
Must have
• Any color used should coordinate with my logo design (see attached files).
• Card should be printed horizontally so top and bottom are longest sides of rectangle.
• Background color or paper color should complement and highlight logo. Do not like a white background. black, grey, brown or any color my logo would blend well with.
Nice to have
• I would like designer to utilize color to highlight letters/name or phone-fax-web symbols.
• Bottom edge of card could be highlighted if appropriate to an idea.
Should not have
• I would NOT want the card to have a pure white background at all.
• No clear cards.
• Cards should be oriented with long sides on bottom and top, NOT sides. DO NOT LIKE THIS THIN TALL ORIENTATION.

```html
<!DOCTYPE html>
<html lang="en">
<head>
<meta charset="utf-8">
<title>Brightfern Wellness – Business Card</title>
<link href="https://fonts.googleapis.com/css2?family=Roboto:wght@400;500;700&display=swap" rel="stylesheet">
<style>
  :root {
    --backdrop: #5b5b5d;
    --card-paper: #f3efe6;
    --brand-blue: #2473b6;
    --ink: #262626;
    --divider: #3f7fc0;
    --on-blue: #ffffff;
  }
  * { box-sizing: border-box; margin: 0; padding: 0; }
  html, body {
    width: 1200px; height: 900px; overflow: hidden;
    background: var(--backdrop);
    font-family: "Roboto", Arial, sans-serif;
  }
  .canvas {
    position: relative; width: 1200px; height: 900px;
    display: flex; align-items: center; justify-content: center; gap: 60px;
  }
  .card {
    width: 500px; height: 286px; border-radius: 14px;
    box-shadow: 0 10px 24px rgba(0,0,0,.35);
    position: relative; overflow: hidden;
  }
  /* Front */
  .card-front { background: var(--card-paper); display: flex; align-items: center; }
  .brand-block {
    width: 205px; height: 100%;
    display: flex; flex-direction: column; align-items: center; justify-content: center; gap: 10px;
  }
  .brand-mark { width: 18px; height: 18px; border-radius: 50%; background: var(--brand-blue); }
  .brand-name {
    color: var(--brand-blue); font-weight: 700; font-size: 25px; line-height: 1.1;
    text-align: center; letter-spacing: .5px;
  }
  .divider { width: 2px; height: 190px; background: var(--divider); flex: none; }
  .details { padding-left: 22px; padding-right: 14px; color: var(--ink); font-size: 13px; line-height: 1.42; }
  .person-name { color: var(--brand-blue); font-weight: 700; font-size: 19px; margin-bottom: 2px; white-space: nowrap; }
  .address { margin-top: 6px; }
  .contact-list { list-style: none; margin-top: 6px; }
  .contact-list li { display: flex; align-items: center; gap: 7px; white-space: nowrap; }
  .contact-icon { width: 12px; height: 12px; flex: none; }
  .contact-icon * { fill: none; stroke: var(--brand-blue); stroke-width: 1.6; }
  .contact-icon .solid { fill: var(--brand-blue); stroke: none; }
  /* Back */
  .card-back {
    background: var(--brand-blue);
    display: flex; flex-direction: column; align-items: center; justify-content: center; gap: 12px;
  }
  .card-back .brand-mark { background: var(--on-blue); width: 22px; height: 22px; }
  .card-back .brand-name { color: var(--on-blue); font-size: 36px; }
</style>
</head>
<body>
<main class="canvas">
  <section class="card card-front" aria-label="Business card front">
    <div class="brand-block">
      <span class="brand-mark"></span>
      <p class="brand-name">Brightfern<br>Wellness</p>
    </div>
    <div class="divider"></div>
    <div class="details">
      <p class="person-name">Gerald M. Whitcombe, Ph.D.</p>
      <p>Licensed Clinical Psychologist</p>
      <p>Integrative Health Coach</p>
      <p class="address">4812 Marlowe Ridge Blvd SE<br>Suite 310, Duluth, GA 30096</p>
      <ul class="contact-list">
        <li>
          <svg class="contact-icon" viewBox="0 0 12 12"><path d="M3 1.5 L4.5 4 L3.5 5 Q5 7.5 7 8.5 L8 7.5 L10.5 9 L9.5 10.8 Q4.5 10 1.4 3 Z" class="solid"/></svg>
          770.415.2983
        </li>
        <li>
          <svg class="contact-icon" viewBox="0 0 12 12"><rect x="1" y="2.5" width="10" height="7" rx="1"/><rect x="3" y="4.5" width="6" height="1.5" class="solid"/></svg>
          770.581.4096
        </li>
        <li>
          <svg class="contact-icon" viewBox="0 0 12 12"><rect x="1" y="2.5" width="10" height="7"/><path d="M1 2.5 L6 7 L11 2.5"/></svg>
          drgeraldwhitcombe@quillmarsh.net
        </li>
        <li>
          <svg class="contact-icon" viewBox="0 0 12 12"><circle cx="6" cy="6" r="5"/><ellipse cx="6" cy="6" rx="2.2" ry="5"/><path d="M1 6 H11"/></svg>
          www.brightfernwellness.net
        </li>
      </ul>
    </div>
  </section>

  <section class="card card-back" aria-label="Business card back">
    <span class="brand-mark"></span>
    <p class="brand-name">Brightfern Wellness</p>
  </section>
</main>
</body>
</html>
```